KRWB new business card design

We need a business card design for our established business which is Australia wide however based in Melbourne. We are a young team of Financial Planners who specialize in Insurance and Basic super advice for people like us.

We are people who help our clients get things done in a timely and cost effective manner whilst having a good time and a laugh along the way.

We would like this to have a consistent feel with our new e-brochure which i have attached from a color and font perspective.

Industry/Entity Type

Business

Requirements
Must have
• We do not need specific address details rather just the states we are in:

VIC/NSW/QLD/TAS
Nice to have
• Curved edge to mate the brochure

```html
<!DOCTYPE html>
<html lang="en">
<head>
<meta charset="utf-8">
<title>KRWB business card design</title>
<link rel="stylesheet" href="https://fonts.googleapis.com/css2?family=Arimo:ital,wght@0,400;0,700;1,700&family=PT+Sans&display=swap">
<style>
  :root {
    --backdrop: #b4875a;
    --label: #2a1a0e;
    --ink-dark: #1c1c1c;
    --ink-deep: #111111;
    --green-bright: #6cc04a;
    --green-deep: #00a651;
    --grey-text: #6d6e70;
    --grey-dark: #414042;
    --white: #ffffff;
  }
  * { margin: 0; padding: 0; box-sizing: border-box; }
  html, body { width: 1200px; height: 788px; overflow: hidden; }
  body {
    position: relative;
    background: var(--backdrop);
    font-family: "Arimo", Arial, sans-serif;
  }
  .view-label {
    position: absolute;
    width: 200px;
    text-align: center;
    font-family: "PT Sans", sans-serif;
    font-size: 22px;
    color: var(--label);
  }
  .card {
    position: absolute;
    width: 527px;
    height: 300px;
    border-radius: 28px 4px 28px 4px;
    overflow: hidden;
    box-shadow: 2px 4px 10px rgba(0,0,0,0.35);
  }
  .card--dark { background: radial-gradient(circle at 30% 40%, #3a3a3a 0%, var(--ink-dark) 55%, var(--ink-deep) 100%); }
  .card--light { background: var(--white); }
  .card--front { left: 53px; top: 72px; border-radius: 4px 28px 28px 4px; }
  .card--back-1 { left: 622px; top: 75px; }
  .card--back-2 { left: 53px; top: 445px; }
  .card--back-3 { left: 622px; top: 445px; }

  .swoosh { position: absolute; inset: 0; }

  .brand {
    position: absolute;
    display: flex;
    flex-direction: column;
    align-items: center;
    gap: 14px;
  }
  .brand__mark { width: 34px; height: 34px; background: var(--green-bright); }
  .brand__name { font-weight: 700; font-size: 46px; letter-spacing: 1px; line-height: 1; }
  .brand--on-dark .brand__name { color: var(--white); }
  .brand--on-light .brand__name { color: var(--ink-deep); }

  .contact { position: absolute; left: 240px; top: 46px; color: var(--white); font-size: 14px; }
  .contact__name { color: var(--green-bright); font-weight: 700; font-size: 18px; }
  .contact__role { color: var(--green-bright); font-weight: 700; font-size: 14px; line-height: 18px; }
  .contact__list { list-style: none; margin-top: 30px; }
  .contact__list li { line-height: 21.6px; }
  .contact__list b { font-style: italic; }

  .services { position: absolute; list-style: none; font-weight: 700; font-size: 14px; }
  .services__title { font-style: italic; font-size: 18px; margin-bottom: 14px; }
  .services li { line-height: 34px; }
  .services li::before { content: "\25AA\00a0"; }
  .services--grey { left: 320px; top: 44px; color: var(--grey-text); }
  .services--grey .services__title { color: var(--grey-text); }
  .services--center { left: 0; right: 0; top: 45px; text-align: center; color: var(--grey-dark); }
  .services--white { left: 314px; top: 24px; color: var(--white); }

  .divider {
    position: absolute; left: 260px; top: 20px; width: 2px; height: 230px;
    background: linear-gradient(to bottom, transparent, #8a8a8a 30%, #8a8a8a 70%, transparent);
  }
  .tagline-band {
    position: absolute; left: 0; right: 0; bottom: 0; height: 40px;
    background: var(--green-bright); color: var(--white);
    font-weight: 700; font-size: 14px; text-align: center; line-height: 40px;
  }
  .tagline {
    position: absolute; left: 0; right: 0; bottom: 15px; text-align: center;
    font-weight: 700; font-size: 14px; color: var(--grey-dark);
  }
  .tagline--green {
    left: 313px; right: auto; bottom: 12px; text-align: left;
    color: var(--green-bright); line-height: 18px;
  }
</style>
</head>
<body>
  <div class="view-label" style="left:220px;top:32px;">Front</div>
  <div class="view-label" style="left:795px;top:32px;">Back - 1</div>
  <div class="view-label" style="left:220px;top:402px;">Back - 2</div>
  <div class="view-label" style="left:795px;top:402px;">Back - 3</div>

  <section class="card card--dark card--front">
    <svg class="swoosh" viewBox="0 0 527 300" width="527" height="300" aria-hidden="true">
      <path d="M350 0 H527 V300 H430 C520 230 540 70 350 0 Z" fill="var(--green-deep)"/>
      <path d="M360 0 C500 60 480 240 430 300 H445 C520 220 520 60 390 0 Z" fill="#0c0c0c"/>
      <path d="M395 0 C520 70 505 230 450 300 H462 C530 220 525 70 420 0 Z" fill="var(--green-bright)" opacity="0.55"/>
    </svg>
    <div class="brand brand--on-dark" style="left:48px;top:92px;">
      <span class="brand__mark"></span>
      <span class="brand__name">KRWB</span>
    </div>
    <div class="contact">
      <p class="contact__name">Daniel Mercer</p>
      <p class="contact__role">ADFS, BBus, LRS©<br>Financial Adviser</p>
      <ul class="contact__list">
        <li><b>cell</b> 0412 555 018</li>
        <li><b>phone</b> 1300 555 742</li>
        <li><b>fax</b> 03 9555 0147</li>
        <li><b>email</b> daniel@krwb.com.au</li>
        <li><b>web</b> www.krwb.com.au</li>
        <li>VIC/NSW/QLD/TAS</li>
      </ul>
    </div>
  </section>

  <section class="card card--light card--back-1">
    <div class="brand brand--on-light" style="left:70px;top:100px;">
      <span class="brand__mark"></span>
      <span class="brand__name">KRWB</span>
    </div>
    <div class="divider"></div>
    <ul class="services services--grey">
      <li class="services__title" style="list-style:none;">Specialising in</li>
      <li>Risk Insurance</li>
      <li>Debt Management</li>
      <li>Superannuation</li>
      <li>Wealth Creation</li>
      <li>Retirement Planning</li>
    </ul>
    <div class="tagline-band">SECURE FUTURE, ENHANCED LIFESTYLE</div>
  </section>

  <section class="card card--light card--back-2">
    <ul class="services services--center">
      <li class="services__title">Specialising in</li>
      <li>Risk Insurance</li>
      <li>Debt Management</li>
      <li>Superannuation</li>
      <li>Wealth Creation</li>
      <li>Retirement Planning</li>
    </ul>
    <p class="tagline">SECURE FUTURE, ENHANCED LIFESTYLE</p>
  </section>

  <section class="card card--dark card--back-3">
    <div class="brand brand--on-dark" style="left:60px;top:100px;">
      <span class="brand__mark"></span>
      <span class="brand__name" style="font-size:54px;">KRWB</span>
    </div>
    <ul class="services services--white">
      <li class="services__title">Specialising in</li>
      <li>Risk Insurance</li>
      <li>Debt Management</li>
      <li>Superannuation</li>
      <li>Wealth Creation</li>
      <li>Retirement Planning</li>
    </ul>
    <p class="tagline tagline--green">SECURE FUTURE<br>ENHANCED LIFESTYLE</p>
  </section>

  <style>
    .services__title::before { content: none !important; }
  </style>
</body>
</html>
```